Website & Logo The full package New Business new design and idea

Word Press

Simple, clean and very professional and approachable if possible

I am looking for a full business concept from logo to colour pallet and everything in between.
Brand new business concept, the successful applicant may continue on as our outsourced point person for all future work.

I will have an animated explainer video going over the four keys to business success Staff, Product & Services, Marketing, Sales and why the need a coach just like a sporting team to stay focused and clear on measurable outcomes.

Just added script (pdf attachment) i will be using for the explainer video at top of site.
Updates

Target Market(s)

Small business owners in Australia

Industry/Entity Type

Business Consultant

Number of Pages Required

1 page

Font styles to use
Sans Serif

Colors

Designer to choose colors to be used in the design.

Requirements
Must have
• Word press using Divi platform
• Ball park as per pdf uploaded
• Must work on all devices
• Social links
• Clear and straight forward movement through site
• Great capture of name and email,
• Free Download
• 10 Things you can start today in your small business to get you going again!
Nice to have
• clean one page potentially
• Free files and resources page
Should not have
• boring old menu and old framing

```html
<!DOCTYPE html>
<html lang="en">
<head>
<meta charset="utf-8">
<title>Clear Path Coach</title>
<link href="https://fonts.googleapis.com/css2?family=Montserrat:wght@500;600;700&family=Open+Sans:wght@400;600;700&display=swap" rel="stylesheet">
<style>
:root{
  --blue:#1a76a5;
  --blue-dark:#14628a;
  --blue-deep:#0f4f72;
  --ink:#1d1d1d;
  --text:#444;
  --muted:#666;
  --paper:#fff;
  --foot:#f1f2f4;
  --dark:#2b2722;
}
*{box-sizing:border-box;margin:0;padding:0}
html,body{width:1200px;height:5133px;overflow:hidden;background:var(--paper)}
body{position:relative;font-family:"Open Sans",Arial,sans-serif;color:var(--text)}
.abs{position:absolute}
h1,h2,h3,.brand,.btn,.nav a{font-family:"Montserrat",Arial,sans-serif}
.btn{position:absolute;background:var(--blue);color:#fff;font-size:18px;font-weight:500;display:flex;align-items:center;justify-content:center;border-radius:2px}
.ph{position:absolute}

/* header */
.site-header{top:0;left:0;width:1200px;height:143px}
.contact-line{font-size:15px;color:#333;line-height:27px}
.brand{font-size:24px;font-weight:700;color:var(--blue)}
.logo-dot{width:42px;height:42px;border-radius:50%;background:var(--blue)}
.nav{top:143px;left:0;width:1200px;height:47px;background:var(--blue);display:flex;justify-content:center;gap:46px;align-items:center;padding-right:20px}
.nav a{color:#fff;font-size:15px;font-weight:600;text-decoration:none}

/* hero */
.hero{top:190px;left:0;width:1200px;height:650px;overflow:hidden}
.hero-photo{width:100%;height:100%;background:linear-gradient(160deg,#3a4a57 0%,#5d6d78 35%,#2c3a46 65%,#7f8d97 100%)}
.hero-title{top:400px;left:0;width:1200px;text-align:center;color:#fff;font-size:55px;font-weight:700;line-height:64px;letter-spacing:1px}
.hero-dots{left:1098px;top:233px;width:12px}
.hero-dots span{display:block;width:10px;height:10px;border-radius:50%;background:#fff;margin-bottom:8px}
.hero-dots span.on{background:var(--blue)}

/* intro blocks */
.side-frame{background:var(--blue)}
.side-label{color:#fff;font-family:"Montserrat",sans-serif;font-weight:700;font-size:28px;line-height:32px;transform:rotate(-90deg);transform-origin:left top;white-space:nowrap}
.photo-frame{border:3px solid #fff;position:absolute}
h2.section-title{font-size:36px;font-weight:600;color:var(--ink)}
.body-copy{font-size:15px;line-height:27px;color:#444}

/* bands */
.band{left:0;width:1200px;background:linear-gradient(120deg,#1a78a8,#1a6f9d 50%,#2384b6)}
.band h2{color:#fff;font-size:36px;font-weight:600;text-align:center;width:1200px}
.band p,.band li{color:#fff}
.snap-list{list-style:none}
.snap-list li{position:relative;padding-left:18px;font-size:17px;line-height:27px}
.snap-list li::before{content:"";position:absolute;left:0;top:10px;border-left:6px solid #fff;border-top:4px solid transparent;border-bottom:4px solid transparent}

/* pricing */
.card{background:#fff;box-shadow:0 0 14px rgba(0,0,0,.18);text-align:center}
.badge{position:absolute;left:50%;transform:translateX(-50%);width:68px;height:68px;border-radius:50%;background:var(--blue);color:#fff;font-family:"Montserrat",sans-serif;font-weight:700;font-size:19px;display:flex;align-items:center;justify-content:center;border:4px solid #cfe3ee}
.card h3{font-size:22px;font-weight:600;color:var(--ink);line-height:27px}
.card p{font-size:15px;line-height:27px;color:#444;text-align:left}
.card .btn{font-size:16px}

.act-list{list-style:none}
.act-list li{font-size:17px;font-weight:700;line-height:43px;color:#fff}

/* subscription */
.subscribe{top:4405px;left:0;width:1200px;height:255px;background:linear-gradient(135deg,#3b332b,#2a2520 50%,#4a4037)}
.field{position:absolute;background:#fff;border-radius:4px;height:36px;font-size:14px;color:#333;padding:9px 12px}

/* footer */
.site-footer{top:4660px;left:0;width:1200px;height:473px;background:var(--foot)}
.foot-head{font-family:"Montserrat",sans-serif;font-weight:600;color:var(--ink)}
.foot-links{list-style:none;font-size:15px;line-height:34px;color:#333}
.foot-contact{font-size:15px;line-height:27px;color:#333}
.social span{display:inline-block;width:16px;height:16px;background:#111;border-radius:50%;margin-left:12px}
</style>
</head>
<body>

<header class="abs site-header">
  <svg class="abs" style="left:102px;top:58px" width="22" height="30" viewBox="0 0 22 30"><path d="M11 1C5.5 1 1 5.3 1 10.7 1 18 11 29 11 29s10-11 10-18.3C21 5.3 16.5 1 11 1z" fill="none" stroke="#1a76a5" stroke-width="2"/><circle cx="11" cy="11" r="3.5" fill="none" stroke="#1a76a5" stroke-width="2"/></svg>
  <div class="abs contact-line" style="left:143px;top:46px">17 Harbour Lane,<br>Ridgeview, NH 03999</div>
  <div class="abs logo-dot" style="left:442px;top:52px"></div>
  <div class="abs brand" style="left:508px;top:58px">Clear Path Coach</div>
  <svg class="abs" style="left:886px;top:60px" width="24" height="24" viewBox="0 0 24 24"><path d="M5 2l4 1 1.5 5-2.5 2c1.2 2.6 3.4 4.8 6 6l2-2.5 5 1.5 1 4-3 3C10 22 2 14 2 5z" fill="none" stroke="#1a76a5" stroke-width="1.6"/></svg>
  <div class="abs contact-line" style="left:924px;top:58px">+1-555-010-2288</div>
</header>

<nav class="abs nav">
  <a href="#">Home</a><a href="#">About Us</a><a href="#">About Me</a><a href="#">Works</a><a href="#">Packages</a><a href="#">Contact Us</a>
</nav>

<section class="abs hero">
  <div class="hero-photo" role="img" aria-label="Business people shaking hands over a desk with charts and papers"></div>
  <svg class="abs" style="left:0;top:500px" width="1200" height="150" viewBox="0 0 1200 150"><path d="M0 20 Q600 205 1200 15 L1200 30 Q600 235 0 40Z" fill="#1a76a5"/><path d="M0 40 Q600 235 1200 30 L1200 150 L0 150Z" fill="#fff"/></svg>
  <div class="abs hero-dots"><span></span><span class="on"></span><span></span></div>
</section>
<h1 class="abs hero-title">WELCOME TO CLEAR<br>PATH COACH</h1>
<div class="btn" style="left:408px;top:555px;width:166px;height:44px">Free Download</div>
<div class="btn" style="left:602px;top:555px;width:166px;height:44px">Watch videos</div>

<!-- intro -->
<section>
  <div class="abs side-frame" style="left:88px;top:908px;width:477px;height:283px"></div>
  <div class="abs side-label" style="left:100px;top:1176px">CLEAR PATH<br>COACH</div>
  <div class="ph" role="img" aria-label="Team meeting around a table in a bright office" style="left:185px;top:925px;width:412px;height:250px;background:linear-gradient(135deg,#b8b1a4,#6f6a62 50%,#cfc8bb)"></div>
  <div class="photo-frame" style="left:205px;top:940px;width:375px;height:222px"></div>
  <h2 class="abs section-title" style="left:638px;top:912px">Clear Path Coach</h2>
  <p class="abs body-copy" style="left:640px;top:970px;width:436px">My Clear Path Coach is here to help, support and turn your small business around, It may not be easy, it may not be pretty, it may not be conventional or what you want to hear but my only goal is to help you succeed in your small business struggling in Australia.</p>
  <div class="btn" style="left:633px;top:1125px;width:150px;height:42px">Read More</div>
</section>

<!-- snapshot -->
<section class="abs band" style="top:1257px;height:488px">
  <h2 class="abs" style="top:57px">Australian Small Business Snapshot</h2>
  <p class="abs" style="left:157px;top:176px;width:420px;font-size:17px;line-height:21px">It’s an extremely sad sign of the times when you’re confronted with a myriad of ‘for lease’ signs in shop&nbsp; windows along major shopping hubs.</p>
  <p class="abs" style="left:157px;top:296px;width:420px;font-size:17px;line-height:21px">While most businesses in Australia are small -- accounting for 97 percent of all businesses -- they’re shutting their doors in alarmingly high numbers</p>
  <p class="abs" style="left:643px;top:167px;font-size:17px">What is the Small Business Failure Rate?</p>
  <ul class="abs snap-list" style="left:625px;top:218px;width:430px">
    <li>20% of small businesses fail in their first year</li>
    <li>30% of small businesses fail in their second year</li>
    <li>50% of small businesses fail after five years in business.</li>
    <li>Finally, 70% of small business owners fail in their 10th year in business</li>
  </ul>
</section>

<!-- giving back -->
<h2 class="abs section-title" style="left:0;width:1200px;text-align:center;top:1796px;font-size:35px">Giving Back Free</h2>
<div class="abs card" style="left:167px;top:1925px;width:273px;height:385px">
  <div class="badge" style="top:20px">Free</div>
  <h3 style="margin-top:115px">Giving Back Free</h3>
  <p style="margin:22px 0 0 35px;width:225px">My Clear Path Coach is offering 4 FREE 12-week coaching one on one support program every 3 months .</p>
  <div class="btn" style="left:76px;top:315px;width:120px;height:32px">Read More</div>
</div>
<div class="abs card" style="left:443px;top:1897px;width:312px;height:443px;z-index:2">
  <div class="badge" style="top:26px">$200</div>
  <h3 style="margin-top:120px">Special Offer -<br>week for 12 weeks</h3>
  <p style="margin:22px 0 0 28px;width:260px">My Clear Path Coach is offering this incredible one on one support program to only 12 small business owners in the first quarter in 2019 at below cost.</p>
  <div class="btn" style="left:98px;top:352px;width:118px;height:32px">Read More</div>
</div>
<div class="abs card" style="left:758px;top:1925px;width:270px;height:385px">
  <div class="badge" style="top:12px">$400</div>
  <h3 style="margin-top:90px">Just A Bit More<br>week for 12 weeks</h3>
  <p style="margin:22px 0 0 22px;width:232px">Very limited on application only just 4 clients per quarter, here&nbsp; we provide additional one on&nbsp; one support each week .</p>
  <div class="btn" style="left:66px;top:313px;width:116px;height:32px">Read&nbsp; More</div>
</div>

<!-- how it works -->
<div class="ph" role="img" aria-label="Team placing sticky notes on a glass wall" style="left:88px;top:2415px;width:449px;height:335px;background:linear-gradient(120deg,#3d3a35,#a59a7a 45%,#d9c870 70%,#5b5446)"></div>
<h2 class="abs section-title" style="left:578px;top:2420px">How it all works</h2>
<p class="abs body-copy" style="left:580px;top:2487px;width:520px;font-size:17px">With your permission I breakdown your business, Staff, Products / Services, Marketing and Sales.<br>Under each of these four key components are up to 30 or more components including your staff training and experience, business financials, public exposure and engagement with target market, current marketing and processes required to make income.</p>
<div class="btn" style="left:580px;top:2708px;width:152px;height:42px">Read More</div>

<!-- activities -->
<section class="abs band" style="top:2812px;height:828px">
  <h2 class="abs" style="top:58px">Activates include</h2>
  <p class="abs" style="left:100px;top:178px;width:1000px;text-align:center;font-size:17px;line-height:21px">Regardless if you’re a My Clear Path Coach <b>Free, Special Offer or Just a Bit More</b>, Small Business Owner you all get one on one direct access to me each week along with mountains of accountable activities to turn your small business around into the dream you had hoped it could be.</p>
  <ul class="abs act-list" style="left:105px;top:287px;width:900px">
    <li>Getting a measurable base line of the financials and existing marketing.</li>
    <li>• Discussing the past ups and downs and looking forward to the future</li>
    <li>• Understanding your product or service and how it fits into the current marketplace.</li>
    <li>• Looking into the staff for potential opportunities or training.</li>
    <li>• Understanding market trends and embracing a SWOT analysis</li>
    <li>• Looking to establish a mastermind local group with a successful business</li>
    <li>• Partnership opportunities</li>
    <li>• Creating and applying marketing objectives</li>
    <li>• How to give more to grow</li>
    <li>• External learning materials applied as per needs such as specific podcast episodes or</li>
    <li>suggested books that relate to a special need to be supported.</li>
  </ul>
</section>

<!-- application -->
<h2 class="abs section-title" style="left:90px;top:3715px">Application</h2>
<p class="abs body-copy" style="left:90px;top:3782px;width:495px;font-size:17px">Placements are strictly limited to 28 per quarter as they are all managed personally for the best possible outcomes. You must have internet access, put the time aside between 1-2 hours a week on video call and be open to change and motivated and accountable to succeed with every scheduled meeting.</p>
<div class="ph" role="img" aria-label="Hand filling in an employment application form with a pen beside glasses" style="left:627px;top:3688px;width:483px;height:287px;background:linear-gradient(135deg,#5a5a5e,#d8d8d6 40%,#eeeeec 70%,#9a9a9c)"></div>

<!-- about me -->
<div class="abs side-frame" style="left:90px;top:4050px;width:478px;height:283px"></div>
<div class="abs side-label" style="left:103px;top:4320px">CLEAR PATH<br>COACH</div>
<div class="ph" role="img" aria-label="Portrait of the coach against a grey wall" style="left:205px;top:4068px;width:382px;height:250px;background:linear-gradient(135deg,#7d8a93,#4e5960 50%,#9aa5ac)"></div>
<div class="photo-frame" style="left:225px;top:4082px;width:348px;height:222px"></div>
<h2 class="abs section-title" style="left:652px;top:4065px">About Me</h2>
<p class="abs body-copy" style="left:652px;top:4138px;width:445px;font-size:17px">I am not superman, I just found myself absorbing information over the past 10 years through some mentors and personal development and see so many small business owners struggling and I got sick of telling myself.</p>
<div class="btn" style="left:650px;top:4278px;width:150px;height:40px">Read More</div>

<!-- subscription -->
<section class="abs subscribe" role="img" aria-label="Dark overhead photo of a working desk">
  <h2 class="abs" style="left:0;width:1200px;text-align:center;top:38px;color:#fff;font-size:36px;font-weight:600">Subscription</h2>
  <div class="field" style="left:130px;top:107px;width:458px">Name</div>
  <div class="field" style="left:623px;top:107px;width:449px">Email</div>
  <div class="btn" style="left:528px;top:175px;width:152px;height:40px">Submit</div>
</section>

<!-- footer -->
<footer class="abs site-footer">
  <div class="abs foot-head" style="left:100px;top:100px;font-size:27px">Clear Path Coach</div>
  <p class="abs" style="left:105px;top:150px;width:310px;font-size:15px;line-height:27px;color:#333">My Clear Path Coach is here to help, support and turn your small business around, It may not be easy, it may not be pretty</p>
  <div class="abs foot-head" style="left:505px;top:100px;font-size:18px">Quick Links</div>
  <ul class="abs foot-links" style="left:505px;top:143px">
    <li>Home</li><li>About Us</li><li>About Me</li><li>Works</li><li>Packages</li><li>Contact Us</li>
  </ul>
  <div class="abs foot-head" style="left:782px;top:97px;font-size:18px">Contact us</div>
  <svg class="abs" style="left:772px;top:153px" width="16" height="22" viewBox="0 0 22 30"><path d="M11 1C5.5 1 1 5.3 1 10.7 1 18 11 29 11 29s10-11 10-18.3C21 5.3 16.5 1 11 1z" fill="#111"/><circle cx="11" cy="11" r="4" fill="#fff"/></svg>
  <div class="abs foot-contact" style="left:800px;top:148px">17 Harbour Lane,<br>Ridgeview, NH 03999</div>
  <svg class="abs" style="left:772px;top:210px" width="18" height="18" viewBox="0 0 24 24"><path d="M5 2l4 1 1.5 5-2.5 2c1.2 2.6 3.4 4.8 6 6l2-2.5 5 1.5 1 4-3 3C10 22 2 14 2 5z" fill="#111"/></svg>
  <div class="abs foot-contact" style="left:800px;top:206px">+1-555-010-2288</div>
  <svg class="abs" style="left:772px;top:255px" width="20" height="15" viewBox="0 0 20 15"><rect x="1" y="1" width="18" height="13" fill="none" stroke="#111" stroke-width="1.6"/><path d="M1 1l9 7 9-7" fill="none" stroke="#111" stroke-width="1.6"/></svg>
  <div class="abs foot-contact" style="left:802px;top:249px">hello@clearpathcoach.example</div>
  <div class="abs" style="left:0;width:1200px;text-align:center;top:350px;font-size:17px;font-weight:700;color:var(--blue)">10 Things you can start today in your small business to get you going again!</div>
  <div class="abs" style="left:90px;top:414px;font-size:17px;color:#333">Copyright © Clear Path Coach</div>
  <div class="abs social" style="left:1002px;top:418px"><span></span><span></span><span></span></div>
</footer>

</body>
</html>
```